Velk Partners Building Business Cards

We need a business card that reflects our business as "Solar Experts" in San Diego. Browse our website www.velkpartners.example our License needs to be displayed as "CSLB# 3867140" our phone number is (619) 555-0187

Save thousands on your electric bills and increase the value of your home while helping to protect the environment. Our solar installation experts will help you design the system that's right for you, using only the highest quality equipment that will look great and give you ideal performance. Our goal is to make you energy independent, and get your electric bill to 0.

Paul Osterby
(619) 555-0187
paul@velkpartners.example

Target Market(s)

Home owners in san diego looking for solar

Industry/Entity Type

Solar Energy

Contact Information for Business Card

Paul Osterby
(619) 555-0187
paul@velkpartners.example

Font styles to use
Other font styles liked:
• Use our logo font

Requirements
Must have
• License needs to be displayed as "CSLB# 3867140" our phone number is (619) 555-0187
Nice to have
• Real images of rooftop home solar in san diego
Should not have
• our business address

```html
<!DOCTYPE html>
<html lang="en">
<head>
<meta charset="utf-8">
<title>Velk Partners Building – Business Cards</title>
<link href="https://fonts.googleapis.com/css2?family=Open+Sans:wght@400;600;700&display=swap" rel="stylesheet">
<style>
  :root {
    --page-bg: #e9ebee;
    --blue-light: #1f6cc0;
    --blue-mid: #1656a8;
    --blue-deep: #0f3f86;
    --navy-text: #1a4f9c;
    --sun-yellow: #f4c21f;
    --card-white: #f7f7f5;
    --white: #ffffff;
  }
  * { box-sizing: border-box; margin: 0; padding: 0; }
  html, body {
    width: 1200px; height: 1000px; overflow: hidden;
    background: var(--page-bg);
    font-family: "Open Sans", Arial, sans-serif;
  }
  .sheet {
    width: 1200px; height: 1000px;
    display: flex; flex-direction: column; align-items: center; justify-content: center;
    gap: 40px;
  }
  .card {
    width: 770px; height: 440px; position: relative; overflow: hidden;
    box-shadow: 0 6px 18px rgba(0,0,0,0.18);
  }
  .blue-surface {
    background: radial-gradient(ellipse at 45% 35%, var(--blue-light) 0%, var(--blue-mid) 55%, var(--blue-deep) 100%);
  }

  /* Front */
  .card-front { display: flex; }
  .front-brand {
    width: 42%; background: var(--card-white);
    display: flex; flex-direction: column; justify-content: center; padding-left: 40px;
  }
  .brand-name {
    font-weight: 700; color: var(--navy-text);
    font-size: 31px; line-height: 1.1; letter-spacing: -0.5px;
  }
  .license {
    margin-top: 16px; font-size: 15px; color: var(--navy-text);
  }
  .front-contact {
    flex: 1; color: var(--white);
    display: flex; flex-direction: column; justify-content: center; padding-left: 48px;
  }
  .person-name {
    font-size: 34px; font-weight: 600; letter-spacing: 1px; text-transform: uppercase;
    margin-bottom: 22px;
  }
  .person-name .surname { color: var(--sun-yellow); }
  .contact-list { list-style: none; font-size: 17px; }
  .contact-list li { display: flex; align-items: center; gap: 12px; margin-bottom: 9px; }
  .contact-list svg { width: 16px; height: 16px; fill: var(--white); flex: none; }
  .accent { color: var(--sun-yellow); }

  /* Back */
  .card-back {
    display: flex; align-items: center; justify-content: center;
  }
  .back-brand {
    font-weight: 700; color: var(--white);
    font-size: 54px; letter-spacing: -0.5px;
  }
  .back-web {
    position: absolute; left: 40px; bottom: 34px;
    font-size: 16px; color: var(--white);
  }
</style>
</head>
<body>
<main class="sheet">
  <section class="card card-front" aria-label="Business card front">
    <div class="front-brand">
      <div class="brand-name">Velk Partners Building</div>
      <div class="license">License-"CSLB# 3867140"</div>
    </div>
    <div class="front-contact blue-surface">
      <div class="person-name">Paul <span class="surname">Osterby</span></div>
      <ul class="contact-list">
        <li>
          <svg viewBox="0 0 24 24" aria-hidden="true"><path d="M6.6 10.8a15.1 15.1 0 0 0 6.6 6.6l2.2-2.2a1 1 0 0 1 1-.25 11.4 11.4 0 0 0 3.6.57 1 1 0 0 1 1 1V20a1 1 0 0 1-1 1A17 17 0 0 1 3 4a1 1 0 0 1 1-1h3.5a1 1 0 0 1 1 1c0 1.25.2 2.45.57 3.6a1 1 0 0 1-.25 1z"/></svg>
          (619) 555-0187
        </li>
        <li>
          <svg viewBox="0 0 24 24" aria-hidden="true"><path d="M2 5h20v14H2zm2 2v.5l8 5 8-5V7zm0 2.8V17h16V9.8l-8 5z"/></svg>
          paul@velkpartners.example
        </li>
        <li>
          <svg viewBox="0 0 24 24" aria-hidden="true"><path d="M12 2a10 10 0 1 0 0 20 10 10 0 0 0 0-20zm6.9 9h-3a15 15 0 0 0-1.3-5.6A8 8 0 0 1 18.9 11zM12 4.1c.9 1.2 1.8 3.6 1.9 6.9h-3.8c.1-3.3 1-5.7 1.9-6.9zM9.4 5.4A15 15 0 0 0 8.1 11h-3a8 8 0 0 1 4.3-5.6zM5.1 13h3a15 15 0 0 0 1.3 5.6A8 8 0 0 1 5.1 13zm6.9 6.9c-.9-1.2-1.8-3.6-1.9-6.9h3.8c-.1 3.3-1 5.7-1.9 6.9zm2.6-1.3a15 15 0 0 0 1.3-5.6h3a8 8 0 0 1-4.3 5.6z"/></svg>
          <span>www.<span class="accent">velkpartners</span>.example</span>
        </li>
      </ul>
    </div>
  </section>

  <section class="card card-back blue-surface" aria-label="Business card back">
    <div class="back-brand">Velk Partners Building</div>
    <div class="back-web">www.<span class="accent">velkpartners</span>.example</div>
  </section>
</main>
</body>
</html>
```